Corporate Business Card

Very professional, Modern, Not to busy, include phone address email, website
(253) 617-4930, 18761 52nd Avenue S, Kent, WA 98047, martin@plumlinegroup.com, varkoworks.com

Target Market(s)

Manufacturing

Industry/Entity Type

Aero, machining, manufacturing, Off road racing

Contact Information for Business Card

Phone, address email, website

```html
<!DOCTYPE html>
<html lang="en">
<head>
<meta charset="utf-8">
<title>Varko Works – Business Card</title>
<link href="https://fonts.googleapis.com/css2?family=Open+Sans:wght@400;600;700&display=swap" rel="stylesheet">
<style>
  :root {
    --backdrop: #8a8a88;
    --navy: #17346b;
    --navy-deep: #213569;
    --navy-mark: #182a58;
    --red: #d4232b;
    --white: #ffffff;
  }
  * { box-sizing: border-box; margin: 0; padding: 0; }
  html, body {
    width: 1200px; height: 801px; overflow: hidden;
    background: var(--backdrop);
    font-family: "Open Sans", Arial, sans-serif;
  }
  .stage {
    width: 1200px; height: 801px;
    display: flex; align-items: center; justify-content: center; gap: 60px;
  }
  .card {
    position: relative;
    width: 520px; height: 297px;
    border-radius: 16px; overflow: hidden;
    box-shadow: 0 10px 24px rgba(0,0,0,.28);
  }
  .card-front { background: var(--white); }
  .card-front .wave { position: absolute; inset: 0; width: 520px; height: 297px; }
  .front-name {
    position: absolute; left: 36px; top: 132px;
    font-size: 28px; font-weight: 700; color: var(--navy);
    letter-spacing: .3px; white-space: nowrap;
  }
  .front-rule {
    position: absolute; left: 40px; top: 180px;
    width: 150px; height: 2px; background: var(--navy);
  }
  .contact {
    position: absolute; right: 26px; top: 58px;
    text-align: right; color: var(--white);
    font-size: 12.5px; line-height: 1.55; white-space: nowrap;
  }
  .contact .company { color: var(--red); font-weight: 700; font-size: 13px; }
  .contact-row { display: flex; justify-content: flex-end; align-items: center; gap: 7px; }
  .contact-row svg { width: 12px; height: 12px; flex: none; }
  .card-back {
    background: var(--navy-deep);
    display: flex; align-items: center; justify-content: center;
  }
  .back-name {
    font-size: 52px; font-weight: 700; color: var(--navy-mark);
    letter-spacing: 1px;
  }
</style>
</head>
<body>
<main class="stage">
  <section class="card card-front">
    <svg class="wave" viewBox="0 0 520 297">
      <path transform="translate(-14,0)" d="M345 -5 C300 40 305 120 265 185 C225 250 140 280 30 302 L540 302 L540 -5 Z" fill="var(--red)"/>
      <path transform="translate(-6,0)" d="M345 -5 C300 40 305 120 265 185 C225 250 140 280 30 302 L540 302 L540 -5 Z" fill="var(--white)"/>
      <path d="M345 -5 C300 40 305 120 265 185 C225 250 140 280 30 302 L540 302 L540 -5 Z" fill="var(--navy)"/>
      <path d="M50 297 C130 282 185 262 212 232 C192 264 140 286 82 297 Z" fill="var(--red)"/>
    </svg>
    <div class="front-name">Varko Works</div>
    <div class="front-rule"></div>
    <div class="contact">
      <div class="company">Varko Works</div>
      <div>18761 52nd Avenue S</div>
      <div>Kent, WA 98047</div>
      <div class="contact-row">(253) 617-4930
        <svg viewBox="0 0 12 12"><circle cx="6" cy="6" r="6" fill="var(--red)"/><path d="M4 3 L5 3 L5.6 4.6 L4.9 5.1 C5.3 6 6 6.7 6.9 7.1 L7.4 6.4 L9 7 L9 8 C6 8.3 3.7 6 4 3 Z" fill="var(--white)"/></svg>
      </div>
      <div class="contact-row">martin@plumlinegroup.com
        <svg viewBox="0 0 12 12"><circle cx="6" cy="6" r="6" fill="var(--red)"/><rect x="3" y="4" width="6" height="4.2" fill="var(--white)"/><path d="M3 4 L6 6.3 L9 4" stroke="var(--red)" stroke-width=".7" fill="none"/></svg>
      </div>
      <div class="contact-row">varkoworks.com
        <svg viewBox="0 0 12 12"><circle cx="6" cy="6" r="6" fill="var(--red)"/><circle cx="6" cy="6" r="3.2" fill="none" stroke="var(--white)" stroke-width=".8"/><path d="M2.8 6 H9.2 M6 2.8 C4.5 4.5 4.5 7.5 6 9.2 M6 2.8 C7.5 4.5 7.5 7.5 6 9.2" stroke="var(--white)" stroke-width=".7" fill="none"/></svg>
      </div>
    </div>
  </section>

  <section class="card card-back">
    <div class="back-name">Varko Works</div>
  </section>
</main>
</body>
</html>
```